Halvern Studio Works New Business Card

I am opening a new division of my business. I am a high end interior designer, and the new business is writing specs for construction projects. It will be marketed to the VERY high end contractor, architects and realtors. The client will actually be the one who pays us and signs the agreement, but it will be the contractor, architect or realtor that will recommend us. I have attached my current card and our previous logo which is still used on some of our paperwork. I would like the new logo to be connected in some way to what we are currently using. We will need to have room on the card for a person's name. I'd like to omit the address as we might be moving the office soon. The web address is www.HalvernStudioWorks.com. For this design, please use my name, Marisol Thornbury.

Target Market(s)

High End Luxury Contractors, Realtors and Architects

Industry/Entity Type

Residential Construction

Contact Information for Business Card

Halvern Studio Works, Phone: 555-214-9087, www.HalvernStudioWorks.com , Marisol Thornbury

Font styles to use
Sans Serif

Colors
ec1f27

Requirements
Must have
• Some visual reference to my current card and logos. Use the colors submitted on the business card I attached.
Nice to have
• A visual reference to my current card and logos. Use the colors submitted on the card I attached.
Should not have
• A physical address

```html
<!DOCTYPE html>
<html lang="en">
<head>
<meta charset="utf-8">
<title>Halvern Studio Works — Business Card</title>
<link rel="stylesheet" href="https://fonts.googleapis.com/css2?family=Open+Sans:wght@400;600;700&display=swap">
<style>
  :root {
    --stage: #150904;
    --card: #ffffff;
    --card-back: #f6f6f7;
    --brand: #8a2f0c;
    --ink-grey: #7f7f80;
    --fold: #e2e2e4;
  }
  * { margin: 0; padding: 0; box-sizing: border-box; }
  html, body {
    width: 1200px; height: 1000px; overflow: hidden;
    background: var(--stage);
    font-family: "Open Sans", Arial, sans-serif;
  }
  .canvas { position: relative; width: 1200px; height: 1000px; }

  .card { position: absolute; left: 260px; width: 683px; }
  .card--front { top: 96px; height: 391px; background: var(--card); }
  .card--back { top: 529px; height: 389px; background: var(--card-back); }

  .brand-square { position: absolute; background: var(--brand); }
  .brand-name {
    position: absolute; color: var(--ink-grey); font-weight: 400;
    white-space: nowrap; text-align: center; letter-spacing: 0.5px;
  }

  .card--front .brand-square { left: 275px; top: 88px; width: 135px; height: 123px; }
  .card--front .brand-name { left: 0; width: 683px; top: 228px; font-size: 44px; }

  .card--back .panel-divider {
    position: absolute; left: 340px; top: 0; width: 2px; height: 389px;
    background: var(--fold);
  }
  .card--back .brand-square { left: 119px; top: 129px; width: 88px; height: 79px; }
  .card--back .brand-name { left: 0; width: 340px; top: 218px; font-size: 26px; }

  .contact { position: absolute; left: 387px; top: 118px; }
  .contact__name { color: var(--brand); font-weight: 700; font-size: 25px; line-height: 1.2; }
  .contact__title { color: var(--ink-grey); font-weight: 600; font-size: 16px; line-height: 22px; margin-top: 3px; }
  .contact__lines { margin-top: 15px; color: var(--ink-grey); font-weight: 600; font-size: 17px; line-height: 25px; }
  .contact__label { color: var(--brand); font-weight: 700; }
</style>
</head>
<body>
<main class="canvas">
  <section class="card card--front" aria-label="Card front">
    <div class="brand-square"></div>
    <div class="brand-name">Halvern Studio Works</div>
  </section>

  <section class="card card--back" aria-label="Card back">
    <div class="brand-square"></div>
    <div class="brand-name">Halvern Studio Works</div>
    <div class="panel-divider"></div>
    <div class="contact">
      <div class="contact__name">Marisol Thornbury</div>
      <div class="contact__title">Professional Specifications<br>for Contractors</div>
      <div class="contact__lines">
        <div><span class="contact__label">Office:</span> 555.214.9087</div>
        <div><span class="contact__label">Cell:</span> 555.380.4172</div>
        <div>www.HalvernStudioWorks.com</div>
      </div>
    </div>
  </section>
</main>
</body>
</html>
```